Brightfield Homes needs a web design and brand identifier

Brightfield Homes is a pioneering approach by Victorian councils and four greenhouse alliances to support low income households to install solar systems with no upfront costs.

Brightfield Homes will commence in May 2017.

Brightfield Homes is looking for a designer to create a website banner incorporating a brand identifier for Brightfield Homes. The brand identifier will be used in Brightfield Homes promotional materials, such as flyers and mail outs.

The website banner and brand identifier should engender trust and confidence in the target group (retirees).

Reason: Hi, Thank you for your work so far. We've been given advice to get a separate logo designed (instead of trying to include this as part of the banner design). Sorry for not realising this until now - we're new to all this. So, I have a couple of preliminary logo designs that are being considered by our project control group. I will forward a copy of the logo once we have it. The project control group is looking for a web design that is unique to Brightfield Homes and a design that draws on the key elements of the program (i.e. it helps people save money and take control). The site should be friendly but not too informal as the target group is seniors. Here's a link to another community energy organisation: www.kindlewattnet.com.au/ Apologies again for the delays. Cheers, Doug

Target Market(s)

Home owning, low income, retirees

Industry/Entity Type

Non Profit

Number of Pages Required

1 page

Font styles to use
Sans Serif

Requirements
Must have
• Use of Brightfield Home name
• Must promote Brightfield Homes as safe, reliable and trustworthy
Nice to have
• Blue - to engender sense of safety and confidence (open to suggestions, though)
• Solar panels / the sun
Should not have
• Anything that is hard to read
• anything that promotes riskyness

```html
<!DOCTYPE html>
<html lang="en">
<head>
<meta charset="utf-8">
<title>Brightfield Homes</title>
<link rel="stylesheet" href="https://fonts.googleapis.com/css2?family=Raleway:wght@400;500;600;700&family=Open+Sans:wght@400;600;700&display=swap">
<style>
:root{
  --navy:#164a7e;
  --navy-dark:#0f3a66;
  --slate:#2b3a4e;
  --blue:#2a7fc4;
  --blue-mid:#3b93d6;
  --cyan:#1aa9d5;
  --cyan-bright:#22b5e0;
  --grey-bg:#e7e7e7;
  --grey-light:#eef0f1;
  --ink:#222;
  --text:#555;
  --white:#fff;
}
*{margin:0;padding:0;box-sizing:border-box}
html,body{width:1200px;height:2769px;overflow:hidden}
body{font-family:"Open Sans",Arial,sans-serif;color:var(--ink);background:var(--white);position:relative}
h1,h2,h3{font-family:"Raleway",Arial,sans-serif;font-weight:500}

/* header */
.site-header{position:absolute;top:0;left:0;width:1200px;height:92px;z-index:5;background:rgba(10,20,30,.72)}
.brand{position:absolute;left:0;top:0;width:445px;height:92px;background:var(--navy);clip-path:polygon(0 0,100% 0,82% 100%,0 100%)}
.brand-name{position:absolute;left:172px;top:28px;font-family:"Raleway",sans-serif;font-weight:700;font-size:31px;color:var(--white);letter-spacing:.3px}
.brand-corner{position:absolute;left:400px;top:58px;width:36px;height:34px;background:var(--cyan);clip-path:polygon(100% 0,100% 100%,0 100%)}
.call{position:absolute;left:683px;top:11px;display:flex;align-items:center;gap:10px;color:var(--white)}
.call-label{font-size:10px;font-weight:600;display:block;line-height:1}
.call-number{font-size:24px;font-weight:600;line-height:1.1}
.quote-btn{position:absolute;left:888px;top:19px;width:138px;height:28px;border-radius:14px;background:var(--cyan);color:var(--white);font-size:11px;font-weight:700;text-align:center;line-height:28px;text-transform:uppercase}
.main-nav{position:absolute;left:576px;top:70px;display:flex;gap:30px;font-size:11px;font-weight:700;color:var(--white);text-transform:uppercase}

/* hero */
.hero{position:absolute;top:0;left:0;width:1200px;height:602px;background:linear-gradient(100deg,#2f4a22 0%,#4d6a33 30%,#8a7c5a 55%,#6f7c4c 75%,#3f5a2a 100%)}
.hero::after{content:"";position:absolute;inset:0;background:linear-gradient(90deg,rgba(0,0,0,.45) 0%,rgba(0,0,0,.15) 55%,rgba(0,0,0,0) 100%)}
.hero-text{position:absolute;left:172px;top:238px;z-index:2;color:var(--white);width:420px}
.hero-kicker{font-family:"Raleway",sans-serif;font-size:23px;font-weight:400;letter-spacing:.5px;line-height:1}
.hero-title{font-family:"Raleway",sans-serif;font-size:62px;font-weight:700;line-height:1;margin-top:6px}
.hero-copy{font-size:16.5px;line-height:26px;margin-top:24px}
.hero-phone{display:flex;align-items:center;gap:12px;font-size:27px;margin-top:22px}

/* section title */
.section-title{text-align:center;font-size:33px;color:var(--ink)}
.section-title::after{content:"";display:block;width:52px;height:2px;background:var(--cyan);margin:14px auto 0}

/* welcome */
.welcome{position:absolute;top:602px;left:0;width:1200px;height:445px}
.welcome .section-title{margin-top:58px}
.video-thumb{position:absolute;left:172px;top:144px;width:428px;height:240px;background:linear-gradient(180deg,#a9c9c4 0%,#8fb2a3 55%,#5d9a8c 100%)}
.play{position:absolute;left:182px;top:88px}
.play-label{position:absolute;left:0;width:100%;top:162px;text-align:center;color:var(--white);font-size:11px;font-weight:700;text-transform:uppercase}
.welcome-copy{position:absolute;left:633px;top:146px;width:355px;font-size:14px;line-height:23px;color:var(--text)}
.welcome-copy p+p{margin-top:22px}

/* how it works */
.how{position:absolute;top:1047px;left:0;width:1200px;height:476px;background:var(--navy)}
.how .section-title{color:var(--white);margin-top:50px;font-size:29px}
.steps{position:absolute;left:172px;top:129px;display:flex;gap:22px}
.step{position:relative;width:197px;height:286px;border:1px solid rgba(255,255,255,.14);border-radius:4px;text-align:center;color:#e6eef7}
.step-num{position:absolute;left:81px;top:-17px;width:34px;height:34px;border-radius:50%;background:var(--cyan);color:var(--white);font-family:"Raleway",sans-serif;font-size:17px;line-height:34px;box-shadow:0 0 0 4px var(--navy)}
.step-icon{margin:48px auto 0;width:64px;height:72px;display:block}
.step-text{font-size:12.5px;line-height:21px;margin:38px 18px 0}

/* eligibility */
.eligible{position:absolute;top:1523px;left:0;width:611px;height:580px;background:var(--grey-bg)}
.tile{position:absolute;width:197px;display:flex;align-items:center;justify-content:center;text-align:center;color:var(--white);font-size:12px;font-weight:700;text-transform:uppercase;line-height:16px;border-radius:28px 28px 28px 0;border:3px solid rgba(255,255,255,.55)}
.tile-homeowners{left:172px;top:90px;height:194px;background:var(--slate);border-radius:28px 28px 28px 0}
.tile-pension{left:384px;top:44px;height:179px;background:var(--blue-mid);border-radius:0 28px 28px 28px}
.tile-home{left:186px;top:301px;height:196px;background:var(--blue);border-radius:28px 28px 0 28px}
.tile-usage{left:399px;top:338px;height:179px;background:var(--cyan-bright);border-radius:28px 0 28px 28px}
.eligible-title{position:absolute;left:425px;top:242px;font-size:27px;line-height:29px;color:var(--ink)}
.eligible-sub{position:absolute;left:425px;top:308px;font-size:12px;color:var(--text)}

.about{position:absolute;top:1523px;left:611px;width:589px;height:580px;background:linear-gradient(180deg,#1f79c9 0%,#4ea3e0 38%,#c9552e 62%,#b9461f 100%)}
.about-title{position:absolute;left:33px;top:50px;color:var(--white);font-size:33px}
.about-copy{position:absolute;left:33px;top:100px;width:355px;color:var(--white);font-size:13.5px;line-height:21px}

/* what next */
.next{position:absolute;top:2103px;left:0;width:1200px;height:173px;background:var(--cyan);text-align:center;color:var(--white)}
.next-title{font-size:27px;font-weight:600;margin-top:30px;color:var(--white)}
.next-title::after{content:"";display:block;width:46px;height:2px;background:var(--white);margin:10px auto 0}
.next-sub{font-size:13px;margin-top:14px}
.next-contact{font-size:24px;font-weight:700;margin-top:8px}
.next-contact .sep{font-weight:400;margin:0 10px}

/* partners */
.partners{position:absolute;top:2276px;left:0;width:1200px;height:229px;background:var(--grey-light)}
.partners-title{text-align:center;font-family:"Raleway",sans-serif;font-size:18px;font-weight:600;margin-top:41px;color:var(--ink)}
.partner-row{position:absolute;top:100px;left:210px;display:flex;gap:55px;align-items:center}
.partner-badge{width:160px;height:70px;border-radius:4px;background:#c9cdd0}

/* footer */
.site-footer{position:absolute;top:2505px;left:0;width:1200px;height:264px;background:var(--navy);color:var(--white);font-size:11px}
.footer-col{position:absolute;top:33px}
.footer-col h4{font-size:11.5px;font-weight:700;text-transform:uppercase;margin-bottom:16px}
.footer-col li{list-style:none;line-height:22px}
.col-links{left:172px}
.col-support{left:295px}
.col-contact{left:415px}
.col-social{left:648px}
.col-news{left:831px}
.contact-item{display:flex;gap:10px;margin-bottom:12px;line-height:16px}
.social-row{display:flex;gap:14px}
.news-field{width:197px;height:30px;background:var(--blue);border:1px solid rgba(255,255,255,.2);margin-bottom:8px;padding-left:10px;line-height:28px;font-size:11px}
.news-btn{width:197px;height:32px;background:var(--cyan);text-align:center;line-height:32px;font-weight:700;font-size:12px;text-transform:uppercase}
.copyright{position:absolute;left:172px;top:240px;font-size:10px}
</style>
</head>
<body>

<section class="hero" role="img" aria-label="Photo of a smiling senior man in a straw hat resting on a garden fence">
  <div class="hero-text">
    <p class="hero-kicker">HELP PENSIONER HOUSEHOLDS TO</p>
    <h1 class="hero-title">SAVE MONEY</h1>
    <p class="hero-copy">and take control of their energy bills by installing an affordable, quality solar system and be part of an Australian first</p>
    <p class="hero-phone">
      <svg width="26" height="26" viewBox="0 0 24 24" fill="none" stroke="#fff" stroke-width="1.6"><path d="M5 3h4l2 5-2.5 1.5a11 11 0 0 0 6 6L16 13l5 2v4a2 2 0 0 1-2 2A16 16 0 0 1 3 5a2 2 0 0 1 2-2z"/></svg>
      0400 555 217
    </p>
  </div>
</section>

<header class="site-header">
  <div class="brand"><span class="brand-name">BRIGHTFIELD HOMES</span></div>
  <div class="brand-corner"></div>
  <div class="call">
    <svg width="24" height="24" viewBox="0 0 24 24" fill="none" stroke="#fff" stroke-width="1.6"><path d="M5 3h4l2 5-2.5 1.5a11 11 0 0 0 6 6L16 13l5 2v4a2 2 0 0 1-2 2A16 16 0 0 1 3 5a2 2 0 0 1 2-2z"/></svg>
    <div><span class="call-label">CALL NOW</span><span class="call-number">0400 555 217</span></div>
  </div>
  <div class="quote-btn">Request a quote</div>
  <nav class="main-nav"><span>Home</span><span>About us</span><span>Services</span><span>How it works</span><span>Contact us</span></nav>
</header>

<section class="welcome">
  <h2 class="section-title">Welcome to Brightfield Homes</h2>
  <div class="video-thumb" role="img" aria-label="Illustration of a small island with solar panels, wind turbines and houses">
    <svg class="play" width="64" height="64" viewBox="0 0 64 64"><circle cx="32" cy="32" r="29" fill="rgba(0,0,0,.15)" stroke="#fff" stroke-width="3"/><path d="M25 19l20 13-20 13z" fill="#fff"/></svg>
    <span class="play-label">Watch video</span>
  </div>
  <div class="welcome-copy">
    <p>We need you Help pensioner households to save money and take control of their energy bills by installing anaffordable, quality solar system and be part of an Australian first.</p>
    <p>Brightfield Homes is a pioneering approach by Victorian councils to support pensioner households to install solar with no upfront costs. We've done the hard work of finding a safe, reliable and quality installer so pensioners don't have to.</p>
  </div>
</section>

<section class="how">
  <h2 class="section-title">How It Works</h2>
  <div class="steps">
    <div class="step">
      <span class="step-num">01</span>
      <svg class="step-icon" viewBox="0 0 64 72" fill="none" stroke="#fff" stroke-width="2"><circle cx="24" cy="34" r="10"/><path d="M24 16v6M24 46v6M6 34h6M8 21l4 4M40 21l-4 4M8 47l4-4"/><path d="M34 38q10 0 12 8h8M50 42v8M54 44h6M54 48h6"/></svg>
      <p class="step-text">Brightfield Homes checks that every person gets a solar system that pays for itself in energy savings from day one</p>
    </div>
    <div class="step">
      <span class="step-num">02</span>
      <svg class="step-icon" viewBox="0 0 64 72" fill="none" stroke="#fff" stroke-width="2"><rect x="16" y="14" width="30" height="34"/><path d="M26 14v34M36 14v34M16 25h30M16 36h30M31 48v6"/><rect x="34" y="50" width="22" height="12"/><path d="M40 50v-3M50 50v-3"/></svg>
      <p class="step-text">Brightfield Homes organises for the solar system to be installed</p>
    </div>
    <div class="step">
      <span class="step-num">03</span>
      <svg class="step-icon" viewBox="0 0 64 72" role="img" aria-label="Line icon of a senior with a walking stick"><rect x="8" y="12" width="48" height="52" rx="8" fill="rgba(255,255,255,.12)"/></svg>
      <p class="step-text">Brightfield Homes supports pensioners to understand and get the most out of solar</p>
    </div>
    <div class="step">
      <span class="step-num">04</span>
      <svg class="step-icon" viewBox="0 0 64 72" fill="none" stroke="#fff" stroke-width="2"><path d="M14 36h36l6 16H8z"/><path d="M32 36v16M11 44h42M23 36l-3 16M41 36l3 16M32 52v10M24 62h16"/><circle cx="25" cy="16" r="4"/><circle cx="39" cy="26" r="4"/><path d="M40 12L24 30"/></svg>
      <p class="step-text">Pensioners gradually pay for cost through their usual rates payments at 0% interest</p>
    </div>
  </div>
</section>

<section class="eligible">
  <div class="tile tile-homeowners">Homeowners</div>
  <div class="tile tile-pension">Pension card<br>holders</div>
  <h2 class="eligible-title">Is My Client<br>Eligible?</h2>
  <p class="eligible-sub">Refer clients who are:</p>
  <div class="tile tile-home">Usually at home<br>from 9am to 5pm</div>
  <div class="tile tile-usage">Average to high<br>electricity users</div>
</section>

<section class="about" role="img" aria-label="Photo of solar panels on an orange tiled roof under a blue sky with the sun">
  <h2 class="about-title">Who is Brightfield Homes?</h2>
  <p class="about-copy">Over 20 Victorian councils have come together with support from the Victorian Government's Clean Power Futures Fund to run the Brightfield Home program.</p>
</section>

<section class="next">
  <h2 class="next-title">What Next?</h2>
  <p class="next-sub">To refer clients or for further information, contact Doug Marsh at Brightfield Homes:</p>
  <p class="next-contact">Call us : 0400 555 217<span class="sep">|</span>Email us : doug.marsh@elmvale.vic.gov.au</p>
</section>

<section class="partners">
  <h2 class="partners-title">Brightfield Homes is a Partnership Between</h2>
  <div class="partner-row">
    <div class="partner-badge" aria-label="Partner alliance"></div>
    <div class="partner-badge" aria-label="Partner alliance"></div>
    <div class="partner-badge" aria-label="Partner alliance"></div>
    <div class="partner-badge" aria-label="Partner alliance"></div>
  </div>
</section>

<footer class="site-footer">
  <div class="footer-col col-links">
    <h4>Quick Links</h4>
    <ul><li>Home</li><li>About Us</li><li>Services</li><li>How It Works</li><li>Contact Us</li></ul>
  </div>
  <div class="footer-col col-support">
    <h4>Support</h4>
    <ul><li>Contact us</li><li>FAQs</li><li>Legal</li><li>Privacy Policy</li><li>Legal</li></ul>
  </div>
  <div class="footer-col col-contact">
    <h4>Contact Us</h4>
    <div class="contact-item">
      <svg width="20" height="20" viewBox="0 0 20 20"><circle cx="10" cy="10" r="9" fill="none" stroke="#fff"/><path d="M10 4a4 4 0 0 1 4 4c0 3-4 8-4 8s-4-5-4-8a4 4 0 0 1 4-4z" fill="#fff"/></svg>
      <span>Your Company LTD.<br>Street Name, 000000<br>City Name</span>
    </div>
    <div class="contact-item">
      <svg width="20" height="20" viewBox="0 0 20 20" fill="none" stroke="#fff"><circle cx="10" cy="10" r="9"/><path d="M7 5h2l1 3-1.3.8a6 6 0 0 0 3 3L12.5 10l3 1v2a1 1 0 0 1-1 1A9 9 0 0 1 6 6a1 1 0 0 1 1-1z"/></svg>
      <span>Phone<br>0400 555 217</span>
    </div>
    <div class="contact-item">
      <svg width="20" height="20" viewBox="0 0 20 20" fill="none" stroke="#fff"><circle cx="10" cy="10" r="9"/><rect x="5" y="7" width="10" height="7"/><path d="M5 7l5 4 5-4"/></svg>
      <span>Email<br>doug.marsh@elmvale.vic.gov.au</span>
    </div>
  </div>
  <div class="footer-col col-social">
    <h4>Get Connected</h4>
    <div class="social-row" aria-label="Social media links">
      <svg width="22" height="22"><circle cx="11" cy="11" r="9" fill="none" stroke="#fff" stroke-width="1.5"/></svg>
      <svg width="22" height="22"><circle cx="11" cy="11" r="9" fill="none" stroke="#fff" stroke-width="1.5"/></svg>
      <svg width="22" height="22"><circle cx="11" cy="11" r="9" fill="none" stroke="#fff" stroke-width="1.5"/></svg>
      <svg width="22" height="22"><circle cx="11" cy="11" r="9" fill="none" stroke="#fff" stroke-width="1.5"/></svg>
    </div>
  </div>
  <div class="footer-col col-news">
    <h4>E-Newsletter Signup</h4>
    <div class="news-field">Name</div>
    <div class="news-field">Email</div>
    <div class="news-btn">Join</div>
  </div>
  <p class="copyright">© 2017 Brightfield Homes. All Rights Reserved</p>
</footer>

</body>
</html>
```